stationary deign for trucking company

im a trucking company looking for a professional set of stationary designs i deliver goods from point a to b
Updates

When submitting stationary designs I need envelope design, letterhead, cards, I’d badge etc

Industry/Entity Type

Trucking Company

Requirements
Must have
• must have letter head, business card, envelope, fax sheet, id badge, folder, thank you card, notebook, invoice sheet.
Nice to have
• nice to have them all custom made (letterhead,envelope, business card, I’d badge etc
Should not have
• must not have prepaid sign want i unique design for items

```html
<!DOCTYPE html>
<html lang="en">
<head>
<meta charset="utf-8">
<title>Corvane Freight Logistics – Stationery Set</title>
<link href="https://fonts.googleapis.com/css2?family=Montserrat:wght@600&family=Roboto:wght@400;500;700&family=Great+Vibes&family=Roboto+Slab:wght@400&display=swap" rel="stylesheet">
<style>
:root{
  --bg:#d7d7d7;
  --paper:#ffffff;
  --paper-soft:#f4f4f4;
  --ink:#1a1a1a;
  --grey:#6b6b6b;
  --blue:#1a4fa0;
  --blue-soft:#aecbea;
  --row:#dfe6ee;
  --black:#0a0a0a;
}
*{box-sizing:border-box;margin:0;padding:0}
html,body{width:1200px;height:828px;overflow:hidden;background:var(--bg);font-family:Roboto,Arial,sans-serif;color:var(--ink)}
.canvas{position:relative;width:1200px;height:828px}
.piece{position:absolute;background:var(--paper);overflow:hidden;box-shadow:0 1px 3px rgba(0,0,0,.18)}
.piece.dark{background:linear-gradient(135deg,#000 0%,#0b0b0b 55%,#3a3a3a 100%);color:#fff}
.label{position:absolute;font-size:7px;letter-spacing:.3px;text-transform:uppercase;color:#333;text-align:center}

/* brand lockup */
.logo{position:absolute;display:flex;align-items:center;gap:5px}
.logo-mark{width:12px;height:12px;border:1.5px solid var(--ink);flex:none}
.logo-name{font-family:Montserrat,Arial,sans-serif;font-weight:600;letter-spacing:1.6px;font-size:10px;line-height:1;color:var(--ink)}
.logo-tag{font-size:3.6px;letter-spacing:1.2px;margin-top:2px;color:var(--ink)}
.logo.lg .logo-mark{width:20px;height:20px;border-width:2px}
.logo.lg .logo-name{font-size:17px;letter-spacing:2.4px}
.logo.lg .logo-tag{font-size:5.6px;letter-spacing:1.8px}
.logo.white .logo-mark{border-color:#fff}
.logo.white .logo-name,.logo.white .logo-tag{color:#fff}
.ghost{position:absolute;font-family:Montserrat,Arial,sans-serif;font-weight:600;color:rgba(26,79,160,.05);letter-spacing:3px;white-space:nowrap}
.dark .ghost{color:rgba(255,255,255,.08)}

/* footer band */
.band{position:absolute;left:0;right:0;bottom:0;height:8px}
.band::before{content:"";position:absolute;left:0;right:30%;bottom:1px;height:2.5px;background:var(--blue)}
.band-tab{position:absolute;right:0;bottom:0;width:34%;height:8px;background:var(--black);clip-path:polygon(7px 0,100% 0,100% 100%,0 100%);color:#fff;font-size:4.8px;line-height:8px;text-align:right;padding-right:5px;white-space:nowrap}

.small{font-size:5px;line-height:1.4;color:var(--grey)}
.contact{position:absolute;font-size:4.4px;line-height:1.35;color:var(--grey);border-left:1.5px solid var(--blue);padding-left:3px}

/* positions */
.card-front{left:53px;top:122px;width:206px;height:118px}
.card-back{left:53px;top:267px;width:206px;height:118px}
.env-back{left:284px;top:123px;width:256px;height:116px}
.env-front{left:284px;top:268px;width:256px;height:116px}
.ty-front{left:570px;top:38px;width:216px;height:158px}
.ty-back{left:570px;top:224px;width:216px;height:158px}
.id-front{left:828px;top:152px;width:150px;height:230px}
.id-back{left:998px;top:152px;width:150px;height:230px}
.sheet{top:414px;width:256px;height:364px}
.letterhead{left:53px}.fax{left:332px}.invoice{left:611px}.notebook{left:892px}

/* business card front */
.holder-name{position:absolute;left:13px;top:54px;font-size:7.6px;font-weight:500;color:var(--blue)}
.holder-role{position:absolute;left:13px;top:63px;font-size:4.6px;font-weight:700}
.card-rule{position:absolute;left:13px;right:13px;top:71px;height:.6px;background:#ccc}
.card-contact{position:absolute;left:13px;top:75px;font-size:4.4px;line-height:6.4px;color:var(--grey)}
.card-address{position:absolute;right:13px;top:88px;text-align:right;font-size:4.4px;line-height:6.4px;color:var(--grey)}

.flap{position:absolute;left:0;right:0;top:0;height:44px;background:linear-gradient(90deg,#000 60%,#3b3b3b);border-radius:0 0 40px 40px}
.fold-edge{position:absolute;background:var(--black);clip-path:polygon(0 0,100% 20%,100% 100%,0 100%)}
.fold-edge.light{background:#ececec;clip-path:polygon(0 0,100% 12%,100% 100%,0 100%)}

.thanks{position:absolute;left:48px;top:82px;font-family:"Great Vibes",cursive;font-size:38px;color:var(--blue)}

/* id badge front */
.id-title{position:absolute;left:0;right:0;top:88px;text-align:center;font-family:"Roboto Slab",serif;font-size:11px;color:var(--blue)}
.photo{position:absolute;left:25px;top:122px;width:45px;height:56px;border-radius:4px;background:var(--blue-soft)}
.id-fields{position:absolute;left:80px;top:122px;font-size:6.4px;line-height:10.3px;color:#555}
.sign{position:absolute;top:206px;font-size:5px;color:#666;white-space:nowrap}

/* fax */
.fax-grid{position:absolute;left:21px;top:82px;width:214px;display:grid;grid-template-columns:30px 76px 30px 78px;gap:1.5px}
.fax-grid div{height:10px;background:#e9e9e9;font-size:4px;line-height:10px;padding-left:3px;color:#555}
.checks{position:absolute;left:22px;top:136px;width:220px;display:flex;justify-content:space-between;font-size:3.4px;color:#555}
.checks span::before,.pay span::before{content:"";display:inline-block;width:4px;height:4px;border:.6px solid #555;margin-right:2px;vertical-align:-1px}
.comments{position:absolute;left:23px;top:148px;font-size:4.2px;color:#555}

/* invoice */
.inv-head{position:absolute;left:26px;width:206px;font-size:3.8px;color:#555}
.inv-head i{display:block;border-bottom:.6px solid #888;margin-top:4px;font-style:normal}
.inv-table{position:absolute;left:25px;top:131px;width:208px;height:145px;border:.8px solid var(--blue);
  background:repeating-linear-gradient(#fff 0 6px,var(--row) 6px 12px);background-position:0 6px}
.inv-th{height:6px;background:var(--blue);color:#fff;font-size:3.4px;line-height:6px;display:grid;grid-template-columns:18px 136px 27px 27px;text-align:center}
.col{position:absolute;top:0;bottom:0;width:.8px;background:var(--blue)}
.totals{position:absolute;left:178px;top:277px;width:55px;border:.8px solid var(--blue);font-size:3.4px;color:#333}
.totals div{height:9px;line-height:9px;padding-left:2px;border-bottom:.6px solid var(--blue);width:28px;border-right:.6px solid var(--blue)}
.pay{position:absolute;left:25px;top:283px;display:flex;gap:9px;font-size:3.4px;color:#555}
.terms{position:absolute;left:25px;top:300px;font-size:3px;line-height:1.3;color:#666}

/* notebook */
.spiral{position:absolute;left:1px;top:0;bottom:0;width:4px;background:repeating-linear-gradient(#777 0 1px,transparent 1px 3px)}
.ruled{position:absolute;left:24px;right:24px;top:70px;height:280px;background:repeating-linear-gradient(transparent 0 9.4px,#9a9a9a 9.4px 10px)}
</style>
</head>
<body>
<div class="canvas">

  <!-- business card front -->
  <section class="piece card-front">
    <div class="ghost" style="left:14px;top:22px;font-size:30px">CORVANE</div>
    <div class="logo" style="left:110px;top:18px"><span class="logo-mark"></span><div><div class="logo-name">CORVANE</div><div class="logo-tag">FREIGHT • LOGISTICS</div></div></div>
    <div class="holder-name">DANIEL REYES</div>
    <div class="holder-role">CEO/FOUNDER</div>
    <div class="card-rule"></div>
    <div class="card-contact">☏ 555 210 4410<br>▯ 555 318 7726<br>▬ 555 462 0193<br>✉ daniel@corvanefreight.com</div>
    <div class="card-address">1420 Birchwood Road<br>Fairview, Alaska 99501</div>
    <div class="band"><div class="band-tab">www.corvanefreight.com</div></div>
  </section>
  <div class="label" style="left:53px;top:250px;width:206px">Front Card</div>

  <!-- business card back -->
  <section class="piece dark card-back">
    <div class="logo white lg" style="left:54px;top:44px"><span class="logo-mark"></span><div><div class="logo-name">CORVANE</div><div class="logo-tag">FREIGHT • LOGISTICS</div></div></div>
    <div style="position:absolute;left:0;right:0;top:102px;text-align:center;font-size:4.6px;letter-spacing:3px;color:#ccc">www.corvanefreight.com</div>
  </section>
  <div class="label" style="left:53px;top:394px;width:206px">Back Card</div>

  <!-- envelope back -->
  <section class="piece env-back" style="background:var(--paper-soft)">
    <div class="flap"></div>
    <div class="logo white" style="left:92px;top:16px"><span class="logo-mark"></span><div class="logo-name" style="font-size:8px">CORVANE</div></div>
  </section>
  <div class="label" style="left:284px;top:250px;width:256px">Envelope Back</div>

  <!-- envelope front -->
  <section class="piece env-front">
    <div class="ghost" style="left:150px;top:48px;font-size:26px">CORVANE</div>
    <div class="logo" style="left:16px;top:16px"><span class="logo-mark"></span><div><div class="logo-name">CORVANE</div><div class="logo-tag">FREIGHT • LOGISTICS</div></div></div>
    <div class="small" style="position:absolute;left:38px;top:36px;font-size:5px">1420 Birchwood Road<br>Fairview, Alaska 99501</div>
    <div class="band"><div class="band-tab">www.corvanefreight.com</div></div>
  </section>
  <div class="label" style="left:284px;top:394px;width:256px">Envelope Front</div>

  <!-- thank you card front -->
  <div class="fold-edge" style="left:786px;top:38px;width:16px;height:148px"></div>
  <section class="piece ty-front">
    <div class="logo lg" style="left:28px;top:34px"><span class="logo-mark"></span><div><div class="logo-name">CORVANE</div><div class="logo-tag">FREIGHT • LOGISTICS</div></div></div>
    <div class="thanks">Thank you</div>
    <div class="band"><div class="band-tab">www.corvanefreight.com</div></div>
  </section>
  <div class="label" style="left:570px;top:206px;width:216px">Thank You Card Front</div>

  <!-- thank you card back -->
  <div class="fold-edge light" style="left:786px;top:224px;width:16px;height:149px"></div>
  <section class="piece dark ty-back">
    <div class="ghost" style="left:52px;top:56px;font-size:26px">CORVANE</div>
    <div style="position:absolute;left:0;right:0;top:128px;text-align:center;font-size:5.2px;line-height:1.4;color:#eee">1420 Birchwood Road, Fairview, Alaska 99501<br>P: 555 210 4410 &nbsp;M: 555 318 7726 &nbsp;F: 555 462 0193<br>E: daniel@corvanefreight.com &nbsp;W: corvanefreight.com</div>
  </section>
  <div class="label" style="left:570px;top:394px;width:216px">Thank You Card Back</div>

  <!-- id badge front -->
  <section class="piece id-front">
    <div class="logo" style="left:14px;top:22px"><span class="logo-mark" style="width:16px;height:16px"></span><div><div class="logo-name" style="font-size:12px">CORVANE</div><div class="logo-tag">FREIGHT • LOGISTICS</div></div></div>
    <div class="id-title">STAFF I.D. CARD</div>
    <div class="photo" role="img" aria-label="Staff photo"></div>
    <div class="id-fields">Your Name<br>Position<br>Date of birth<br>Sex<br>Blood group<br>Valid up to :</div>
    <div class="sign" style="left:10px">Card holder signature</div>
    <div class="sign" style="right:10px">Authorised signature</div>
    <div class="band"><div class="band-tab" style="width:50%">www.corvanefreight.com</div></div>
  </section>
  <div class="label" style="left:828px;top:394px;width:150px">ID Badge Front</div>

  <!-- id badge back -->
  <section class="piece dark id-back">
    <div class="logo white lg" style="left:22px;top:72px"><span class="logo-mark"></span><div><div class="logo-name">CORVANE</div><div class="logo-tag">FREIGHT • LOGISTICS</div></div></div>
    <div style="position:absolute;left:0;right:0;top:156px;text-align:center;font-size:5.4px;line-height:1.4;color:#eee">1420 Birchwood Road,<br>Fairview, Alaska 99501<br><br>P: 555 210 4410<br>M: 555 318 7726 F: 555 462 0193<br>E: daniel@corvanefreight.com<br><br>WWW.CORVANEFREIGHT.COM</div>
  </section>
  <div class="label" style="left:998px;top:394px;width:150px">ID Badge Back</div>

  <!-- letterhead -->
  <section class="piece sheet letterhead">
    <div class="ghost" style="left:40px;top:185px;font-size:40px">CORVANE</div>
    <div class="logo" style="left:26px;top:36px"><span class="logo-mark"></span><div><div class="logo-name" style="font-size:8px">CORVANE</div><div class="logo-tag">FREIGHT • LOGISTICS</div></div></div>
    <div class="contact" style="left:178px;top:22px">1420 Birchwood Road<br>Fairview, Alaska 99501<br>☏ 555 210 4410<br>▯ 555 318 7726<br>▬ 555 462 0193<br>✉ daniel@corvanefreight.com</div>
    <div class="band"><div class="band-tab" style="width:28%">www.corvanefreight.com</div></div>
  </section>
  <div class="label" style="left:53px;top:791px;width:256px">Letterhead A4</div>

  <!-- fax -->
  <section class="piece sheet fax">
    <div class="ghost" style="left:50px;top:232px;font-size:40px">CORVANE</div>
    <div class="logo" style="left:26px;top:36px"><span class="logo-mark"></span><div><div class="logo-name" style="font-size:8px">CORVANE</div><div class="logo-tag">FREIGHT • LOGISTICS</div></div></div>
    <div class="contact" style="left:178px;top:22px">1420 Birchwood Road<br>Fairview, Alaska 99501<br>☏ 555 210 4410<br>▯ 555 318 7726<br>▬ 555 462 0193<br>✉ daniel@corvanefreight.com</div>
    <div class="fax-grid">
      <div>To</div><div></div><div>From</div><div></div>
      <div>Fax</div><div></div><div>Pages</div><div></div>
      <div>Phone</div><div></div><div>Date</div><div></div>
      <div>Re</div><div></div><div>CC</div><div></div>
    </div>
    <div class="checks"><span>Urgent</span><span>For Review</span><span>Please comment</span><span>Please reply</span><span>Please recycle</span></div>
    <div class="comments">Comments :</div>
    <div class="band"><div class="band-tab" style="width:28%">www.corvanefreight.com</div></div>
  </section>
  <div class="label" style="left:332px;top:791px;width:256px">Fax A4</div>

  <!-- invoice -->
  <section class="piece sheet invoice">
    <div class="logo" style="left:26px;top:36px"><span class="logo-mark"></span><div><div class="logo-name" style="font-size:8px">CORVANE</div><div class="logo-tag">FREIGHT • LOGISTICS</div></div></div>
    <div class="contact" style="left:178px;top:22px">1420 Birchwood Road<br>Fairview, Alaska 99501<br>☏ 555 210 4410<br>▯ 555 318 7726<br>▬ 555 462 0193<br>✉ daniel@corvanefreight.com</div>
    <div class="inv-head" style="top:92px">INVOICE # : <span style="position:absolute;left:154px">DATE :</span></div>
    <div class="inv-head" style="top:98px"><i>Customer:</i><i>Address:</i><i>Phone: <span style="position:absolute;left:112px">Fax :</span></i></div>
    <div class="inv-table">
      <div class="inv-th"><span>QTY</span><span>DESCRIPTION</span><span>PRICE</span><span>AMOUNT</span></div>
      <div class="col" style="left:17px"></div><div class="col" style="left:153px"></div><div class="col" style="left:180px"></div>
    </div>
    <div class="pay"><span>VISA</span><span>MC</span><span>DEBIT</span><span>CASH</span><span>CHEQUE</span></div>
    <div class="totals"><div>SUB TOTAL</div><div>GST #</div><div style="border-bottom:0">SUBTOTAL</div></div>
    <div class="terms">Signature below indicates<br>acceptance of price and terms</div>
    <div class="band"><div class="band-tab" style="width:28%">www.corvanefreight.com</div></div>
  </section>
  <div class="label" style="left:611px;top:791px;width:256px">Invoice A4</div>

  <!-- notebook -->
  <section class="piece sheet notebook">
    <div class="spiral"></div>
    <div class="ghost" style="left:40px;top:192px;font-size:40px">CORVANE</div>
    <div class="logo" style="left:26px;top:36px"><span class="logo-mark"></span><div><div class="logo-name" style="font-size:8px">CORVANE</div><div class="logo-tag">FREIGHT • LOGISTICS</div></div></div>
    <div class="contact" style="left:178px;top:22px">1420 Birchwood Road<br>Fairview, Alaska 99501<br>☏ 555 210 4410<br>▯ 555 318 7726<br>▬ 555 462 0193<br>✉ daniel@corvanefreight.com</div>
    <div class="ruled"></div>
    <div class="band"><div class="band-tab" style="width:28%">www.corvanefreight.com</div></div>
  </section>
  <div class="label" style="left:892px;top:793px;width:256px">Notebook</div>

</div>
</body>
</html>
```